Concise,Good colour matching,Good looks design for "HERD SCAN QUICK ASSAY FOR LIVESTOCK"

Product Positioning: Affordable test for Large Animals (Livestock/Veterinary Use)
Product Name: HERD SCAN Quick Assay Kit (for large animals, e.g., cattle, horses, swine,Avian,sheep).

2. Packaging Requirements

A. Visual Design
Color Scheme:
Green/Blue/Orange/Yellow/Red/Gray/White(chose 2~4 colors)

Mandatory Info:
Brand logo ("HERD SCAN")

Target Market(s)

Southeast Asia, Africa, Middle East, South America

Industry/Entity Type

Veterinary diagnostic for LIVESTOCK

Colors

Designer to choose colors to be used in the design.

Requirements
Nice to have
• Concise,Good colour matching,Good looks

```html
<!DOCTYPE html>
<html lang="en">
<head>
<meta charset="utf-8">
<title>HERD SCAN Quick Assay Kit – Box Dieline</title>
<link rel="stylesheet" href="https://fonts.googleapis.com/css2?family=Montserrat:wght@400;600;700;800;900&display=swap">
<style>
  :root {
    --navy: #003087;
    --green: #17a01e;
    --green-dark: #0d5e12;
    --green-light: #5fc25a;
    --white: #ffffff;
    --line: #222222;
    --ink: #111111;
  }
  html, body {
    margin: 0;
    padding: 0;
    width: 949px;
    height: 1200px;
    overflow: hidden;
    background: var(--white);
  }
  .dieline { display: block; width: 949px; height: 1200px; }
  .panel { fill: var(--navy); }
  .cut { fill: none; stroke: var(--line); stroke-width: 1.2; }
  .flap { fill: var(--white); stroke: var(--line); stroke-width: 1.2; }
  text { font-family: 'Montserrat', sans-serif; }
  .brand { font-weight: 900; letter-spacing: -0.5px; }
  .brand--white { fill: var(--white); }
  .brand--green { fill: var(--green); }
  .brand--navy { fill: var(--navy); }
  .info { fill: var(--white); font-weight: 700; font-size: 10px; }
  .tagline { fill: var(--white); font-weight: 700; }
  .rapid { fill: var(--green); font-weight: 600; font-size: 12px; letter-spacing: 0.5px; }
  .feature { fill: var(--white); font-size: 6.2px; font-weight: 400; }
  .feature b { font-weight: 700; }
  .dim-line { stroke: var(--ink); stroke-width: 1; }
  .dim-label { fill: var(--ink); font-family: 'Montserrat', sans-serif; font-weight: 400; font-size: 24px; }
</style>
</head>
<body>
<svg class="dieline" viewBox="0 0 949 1200" xmlns="http://www.w3.org/2000/svg">
  <defs>
    <marker id="arrow" viewBox="0 0 10 10" refX="9" refY="5" markerWidth="7" markerHeight="7" orient="auto-start-reverse">
      <path d="M0,0 L10,5 L0,10 z" fill="#111"/>
    </marker>
    <linearGradient id="photo-a" x1="0" y1="0" x2="0" y2="1">
      <stop offset="0" stop-color="#3f9a3a"/><stop offset="1" stop-color="#1f6a1c"/>
    </linearGradient>
    <linearGradient id="photo-b" x1="0" y1="0" x2="0" y2="1">
      <stop offset="0" stop-color="#8fd08a"/><stop offset="1" stop-color="#2e7a2a"/>
    </linearGradient>
    <linearGradient id="photo-c" x1="0" y1="0" x2="1" y2="1">
      <stop offset="0" stop-color="#1c5c18"/><stop offset="1" stop-color="#0e3a0c"/>
    </linearGradient>
  </defs>

  <!-- Dust flaps -->
  <path class="flap" d="M287,82 H252 Q238,82 238,96 V255 Q238,268 250,272 L270,282 H287"/>
  <path class="flap" d="M662,82 H697 Q711,82 711,96 V255 Q711,268 699,272 L679,282 H662"/>
  <path class="flap" d="M287,758 H252 Q238,758 238,744 V585 Q238,572 250,568 L270,558 H287"/>
  <path class="flap" d="M662,758 H697 Q711,758 711,744 V585 Q711,572 699,568 L679,558 H662"/>

  <!-- Side tuck tabs -->
  <polygon class="flap" points="56,291 87,282 87,558 56,549"/>
  <polygon class="flap" points="894,291 862,282 862,558 894,549"/>

  <!-- Glue flap -->
  <path class="flap" d="M287,1031 V1069 Q287,1081 299,1081 H650 Q662,1081 662,1069 V1031"/>

  <!-- Printed panels -->
  <rect class="panel" x="287" y="82" width="375" height="200"/>
  <rect class="panel" x="287" y="282" width="375" height="276"/>
  <rect class="panel" x="87" y="282" width="200" height="276"/>
  <rect class="panel" x="662" y="282" width="200" height="276"/>
  <rect class="panel" x="287" y="558" width="375" height="199"/>

  <!-- Top lid -->
  <g class="lid">
    <text class="brand brand--white" x="465" y="206" font-size="30" text-anchor="middle">HERD SCAN</text>
    <text class="info" x="465" y="231" text-anchor="middle">Manufactured by FIELDWELL</text>
    <text class="info" x="465" y="244" text-anchor="middle">Storage: 2-30 °C,Do not freeze</text>
    <text class="info" x="465" y="257" text-anchor="middle">See the instructions for other contents</text>
  </g>

  <!-- Bottom lid (upside down) -->
  <g class="lid lid--inverted" transform="rotate(180 474.5 420)">
    <text class="brand brand--white" x="465" y="206" font-size="30" text-anchor="middle">HERD SCAN</text>
    <text class="info" x="465" y="231" text-anchor="middle">Manufactured by FIELDWELL</text>
    <text class="info" x="465" y="244" text-anchor="middle">Storage: 2-30 °C,Do not freeze</text>
    <text class="info" x="465" y="257" text-anchor="middle">See the instructions for other contents</text>
  </g>

  <!-- Main face -->
  <g class="front">
    <text class="brand brand--white" x="474.5" y="410" font-size="26" text-anchor="middle">HERD SCAN</text>
    <text class="tagline" x="474.5" y="436" font-size="14" text-anchor="middle">Affordable Diagnostics</text>
    <text class="tagline" x="474.5" y="452" font-size="14" text-anchor="middle">for Healthy Herds</text>
  </g>

  <!-- Left side -->
  <g class="side side--left">
    <text class="brand brand--white" transform="translate(142 440) rotate(-90)" font-size="21">HERD SCAN</text>
    <text class="tagline" transform="translate(245 547) rotate(-90)" font-size="11">Affordable Diagnostics</text>
    <text class="tagline" transform="translate(257 547) rotate(-90)" font-size="11">for Healthy Herds</text>
  </g>

  <!-- Right side -->
  <g class="side side--right">
    <text class="rapid" transform="translate(820 292) rotate(90)">RAPID TEST</text>
    <text class="brand brand--white" transform="translate(818 410) rotate(90)" font-size="21">HERD SCAN</text>
    <text class="feature" transform="translate(762 294) rotate(90)"><tspan font-weight="700">Fast &amp; Efficient:</tspan> Rapid test results in less than</text>
    <text class="feature" transform="translate(754 294) rotate(90)">10 minutes from prep to completion</text>
    <text class="feature" transform="translate(740 294) rotate(90)"><tspan font-weight="700">Affordable:</tspan> Colloidal gold-based rapid tests</text>
    <text class="feature" transform="translate(732 294) rotate(90)">that combine high accuracy</text>
    <text class="feature" transform="translate(724 294) rotate(90)">with cost-effectiveness.</text>
    <text class="feature" transform="translate(708 294) rotate(90)"><tspan font-weight="700">Reliable &amp; Simple:</tspan> Stable test performance</text>
    <text class="feature" transform="translate(700 294) rotate(90)">with 2-30 °C. Easy to operate, no professional</text>
    <text class="feature" transform="translate(692 294) rotate(90)">skills required.</text>
  </g>

  <!-- Back face: livestock photo grid -->
  <g class="photo-grid">
    <rect x="287" y="757" width="125" height="96" fill="url(#photo-a)" role="img" aria-label="Photo of a galloping horse in a grass field, green duotone"/>
    <rect x="412" y="757" width="125" height="96" fill="url(#photo-b)" role="img" aria-label="Photo of a cow standing in a pasture under a cloudy sky, green duotone"/>
    <rect x="537" y="757" width="125" height="96" fill="url(#photo-c)" role="img" aria-label="Photo of a rooster, green duotone"/>
    <rect x="287" y="853" width="125" height="96" fill="url(#photo-a)" role="img" aria-label="Photo of a pig in a field, green duotone"/>
    <rect x="412" y="853" width="125" height="96" fill="url(#photo-c)" role="img" aria-label="Photo of white ducks on grass, green duotone"/>
    <rect x="537" y="853" width="125" height="96" fill="url(#photo-a)" role="img" aria-label="Photo of sheep with lambs in a meadow, green duotone"/>
  </g>
  <rect class="panel" x="287" y="949" width="375" height="41"/>
  <text class="tagline" x="307" y="966" font-size="13">Affordable Diagnostics</text>
  <text class="tagline" x="307" y="980" font-size="13">for Healthy Herds</text>
  <rect x="287" y="990" width="375" height="41" fill="var(--white)"/>
  <text class="brand brand--navy" x="633" y="1011" font-size="21" text-anchor="end">HERD SCAN</text>

  <!-- Cut / fold lines -->
  <g class="cut">
    <rect x="287" y="82" width="375" height="949"/>
    <rect x="87" y="282" width="775" height="276"/>
    <line x1="287" y1="282" x2="662" y2="282"/>
    <line x1="287" y1="558" x2="662" y2="558"/>
    <line x1="287" y1="757" x2="662" y2="757"/>
    <line x1="287" y1="1031" x2="662" y2="1031"/>
  </g>

  <!-- Dimensions -->
  <g class="dimensions">
    <line class="dim-line" x1="728" y1="566" x2="728" y2="750" marker-start="url(#arrow)" marker-end="url(#arrow)"/>
    <text class="dim-label" transform="translate(742 616) rotate(90)">80mm</text>
    <line class="dim-line" x1="728" y1="760" x2="728" y2="1028" marker-start="url(#arrow)" marker-end="url(#arrow)"/>
    <text class="dim-label" transform="translate(742 856) rotate(90)">110mm</text>
    <line class="dim-line" x1="288" y1="1104" x2="661" y2="1104" marker-start="url(#arrow)" marker-end="url(#arrow)"/>
    <text class="dim-label" x="470" y="1144" text-anchor="middle">150mm</text>
  </g>
</svg>
</body>
</html>
```